Hot optical boutique needs a very creative mag ad!

I need a magazine ad in the following size:
Full page trim size = 9” W x 10.875” H
(bleed size = 9.25” W x 11.125” H)

I attached my logo, and another ad which you can get my address, directions off of. I also attached various pictures you are to use.
The purpose of this ad is as follows: We are a high fashion store that just returned from our buying trip in Paris and want to give our customers a peek at what we bought for them.
The title could be: We got back from Paris and our 2016 collections have arrived!

Target Market(s)

Fashionistas!

Industry/Entity Type

Boutique

Font styles to use
Sans Serif

Requirements
Must have
• See in description.
Nice to have
• ?
Should not have
• ?

```html
<!DOCTYPE html>
<html lang="en">
<head>
<meta charset="utf-8">
<title>Laurel Opticians – 2016 Collections</title>
<link href="https://fonts.googleapis.com/css2?family=Jost:wght@400;500&family=Arimo:wght@400&display=swap" rel="stylesheet">
<style>
  :root {
    --paper: #ffffff;
    --ink: #111111;
    --bronze: #5f4b25;
    --rule-grey: #bdbdbd;
    --star-grey: #5a5a5a;
    --brand-red: #e0262c;
    --lens-light: #e9e2a8;
    --lens-mid: #c9b85c;
    --lens-dark: #9c8a3a;
  }
  * { margin: 0; padding: 0; box-sizing: border-box; }
  html, body { width: 1200px; height: 959px; overflow: hidden; background: var(--paper); }
  .ad {
    position: relative;
    width: 1200px;
    height: 959px;
    background: var(--paper);
    font-family: "Jost", sans-serif;
    color: var(--ink);
  }
  .headline { font-weight: 500; text-transform: uppercase; }
  .headline span {
    position: absolute;
    left: 0;
    width: 1188px;
    text-align: center;
    line-height: 1;
    white-space: nowrap;
  }
  .headline .lead   { top: 83px;  font-size: 24px; letter-spacing: 0.5px; }
  .headline .city   { top: 105px; font-size: 88px; color: var(--bronze); }
  .headline .joiner { top: 191px; font-size: 50px; }
  .headline .year   { top: 228px; font-size: 103px; color: var(--bronze); }
  .headline .tail-one { top: 333px; font-size: 36px; }
  .headline .tail-two { top: 373px; font-size: 33px; }

  .divider { position: absolute; left: 472px; top: 421px; width: 246px; height: 22px; }

  .product-photo {
    position: absolute;
    left: 335px; top: 494px;
    width: 519px; height: 220px;
    border-radius: 40px 40px 60px 60px / 20px 20px 80px 80px;
    background: radial-gradient(ellipse at 50% 30%, var(--lens-light) 0%, var(--lens-mid) 60%, var(--lens-dark) 100%);
  }

  .footer { position: absolute; left: 394px; top: 792px; height: 68px; display: flex; align-items: center; }
  .brand { display: flex; align-items: center; gap: 6px; width: 131px; }
  .brand-mark { width: 12px; height: 12px; background: var(--brand-red); flex: none; }
  .brand-name { font-family: "Jost", sans-serif; font-weight: 500; font-size: 11.5px; color: var(--brand-red); letter-spacing: 0.3px; white-space: nowrap; }
  .footer-rule { width: 1px; height: 66px; background: var(--ink); margin-right: 16px; }
  .contact { font-family: "Arimo", sans-serif; font-size: 10px; line-height: 13.5px; color: var(--ink); font-style: normal; }
  .contact .address { text-transform: uppercase; }

  .base-band { position: absolute; left: 253px; top: 896px; width: 684px; height: 5px; background: var(--bronze); }
</style>
</head>
<body>
<main class="ad">
  <h1 class="headline">
    <span class="lead">We got back from</span>
    <span class="city">Paris</span>
    <span class="joiner">and our</span>
    <span class="year">2016</span>
    <span class="tail-one">Collections</span>
    <span class="tail-two">have arrived!</span>
  </h1>

  <svg class="divider" viewBox="0 0 246 22" aria-hidden="true">
    <line x1="0" y1="11" x2="82" y2="11" stroke="var(--rule-grey)" stroke-width="1.5"/>
    <line x1="164" y1="11" x2="246" y2="11" stroke="var(--rule-grey)" stroke-width="1.5"/>
    <polygon points="100,5 101.9,9.4 106.5,9.6 102.9,12.5 104.1,17 100,14.4 95.9,17 97.1,12.5 93.5,9.6 98.1,9.4" fill="var(--star-grey)"/>
    <polygon points="123,1 125.6,7.4 132.5,7.8 127.2,12.2 128.9,18.9 123,15.2 117.1,18.9 118.8,12.2 113.5,7.8 120.4,7.4" fill="var(--bronze)"/>
    <polygon points="146,5 147.9,9.4 152.5,9.6 148.9,12.5 150.1,17 146,14.4 141.9,17 143.1,12.5 139.5,9.6 144.1,9.4" fill="var(--star-grey)"/>
  </svg>

  <div class="product-photo" role="img" aria-label="Product photo of gold mirrored shield sunglasses with thin gold temples"></div>

  <footer class="footer">
    <div class="brand">
      <span class="brand-mark"></span>
      <span class="brand-name">LAUREL OPTICIANS</span>
    </div>
    <div class="footer-rule"></div>
    <address class="contact">
      <div>555.210.4470 &nbsp;|&nbsp; Open Mon-Wed 10-6 Thur-Sat 10-9</div>
      <div class="address">Shops at Harbor Point on Meridian Way</div>
      <div>Next to Casa Verde Tacos and Olivo Restaurant</div>
    </address>
  </footer>

  <div class="base-band"></div>
</main>
</body>
</html>
```